An awsome Vento salt flyer!

We need a professional looking flyer for our mineralsalt product. Named "Vento salt" coming from Maras Peru from the "Terrazales". I have an example but it's not professional looking yet. I hope you can make an amazing flyer for us! valecrestafoods.com is our webpage.
Target Market(s)
Bio shoppers, natural food lovers, healty food lovers,
Industry/Entity Type
Food Store
Requirements
Nice to have
- We would like to have a really nice professionally looking flyer. For the common flyer sizes like DL and A5. I uploaded some bag pictures too. They will be improved soon but its nice to show the product as well. The pink and yellow colors we use in the logo and package would be nice as well.

```html
<!DOCTYPE html>
<html lang="nl">
<head>
<meta charset="utf-8">
<title>Vento Zout flyer</title>
<link href="https://fonts.googleapis.com/css2?family=Jost:wght@400;500;600;700;800&display=swap" rel="stylesheet">
<style>
  :root {
    --stage: #8a8a8a;
    --yellow: #f5c731;
    --yellow-deep: #d9a91c;
    --pink: #e0096f;
    --pink-deep: #b80a5a;
    --ink: #1c1a17;
    --ink-soft: #3b352a;
    --cream: #f3e6b8;
    --paper: #f4f2ee;
  }
  * { box-sizing: border-box; margin: 0; padding: 0; }
  html, body { width: 1200px; height: 1200px; overflow: hidden; }
  body {
    background: radial-gradient(circle at 50% 40%, #a4a4a4, var(--stage) 75%);
    font-family: "Jost", sans-serif;
    color: var(--ink);
    position: relative;
  }
  .flyer {
    position: absolute;
    left: 200px; top: 35px;
    width: 800px; height: 1130px;
    overflow: hidden;
    background: var(--cream);
    box-shadow: 0 12px 40px rgba(0,0,0,.35);
  }
  .flyer-shapes { position: absolute; inset: 0; }
  .title {
    position: absolute; left: 40px; top: 140px;
    font-size: 100px; font-weight: 700; letter-spacing: -1px;
    color: var(--yellow); line-height: 1;
    text-shadow: 0 3px 8px rgba(0,0,0,.35);
  }
  .tagline {
    position: absolute; left: 50px; top: 268px;
    font-size: 25px; font-weight: 600; color: var(--ink);
    line-height: 1.2;
  }
  .intro {
    position: absolute; left: 40px; top: 580px; width: 520px;
    font-size: 19px; font-weight: 600; line-height: 1.25; color: var(--ink);
  }
  .product-name {
    position: absolute; left: 40px; top: 660px;
    font-size: 38px; font-weight: 800; color: var(--ink); line-height: 1.2;
  }
  .product-lead {
    position: absolute; left: 44px; top: 714px; width: 360px;
    font-size: 19px; font-weight: 400; line-height: 1.2; color: var(--ink-soft);
  }
  .minerals {
    position: absolute; left: 50px; top: 768px;
    display: grid; grid-template-columns: 160px 200px; row-gap: 2px;
    list-style: none; font-size: 22px; font-weight: 700; line-height: 1.3;
  }
  .minerals li::before { content: "\25C6"; font-size: 11px; margin-right: 9px; vertical-align: middle; }
  .minerals .dose { font-size: 15px; font-weight: 400; margin-left: 8px; }
  .benefits {
    position: absolute; left: 70px; top: 878px;
    list-style: none; font-size: 19px; font-weight: 600; line-height: 1.2;
  }
  .benefits li { display: flex; gap: 10px; margin-bottom: 6px; }
  .benefits svg { flex: none; margin-top: 5px; }
  .brand {
    position: absolute; right: 30px; top: 1010px;
    text-align: right;
  }
  .brand-name { font-size: 42px; font-weight: 600; color: var(--yellow-deep); line-height: 1; }
  .brand-url { margin-top: 12px; font-size: 18px; font-weight: 600; color: var(--ink); }
</style>
</head>
<body>
<article class="flyer">
  <svg class="flyer-shapes" width="800" height="1130" viewBox="0 0 800 1130">
    <defs>
      <linearGradient id="valley" x1="0" y1="0" x2="0" y2="1">
        <stop offset="0" stop-color="#8ea4bd"/>
        <stop offset=".35" stop-color="#5d5a5e"/>
        <stop offset=".7" stop-color="#8c7b6a"/>
        <stop offset="1" stop-color="#b7ab9a"/>
      </linearGradient>
      <linearGradient id="saltbed" x1="0" y1="0" x2="1" y2="1">
        <stop offset="0" stop-color="#e9d58a"/>
        <stop offset=".6" stop-color="#dcc070"/>
        <stop offset="1" stop-color="#f0e2b0"/>
      </linearGradient>
      <linearGradient id="terraces" x1="0" y1="0" x2="1" y2="1">
        <stop offset="0" stop-color="#efe9e2"/>
        <stop offset="1" stop-color="#c7a67a"/>
      </linearGradient>
      <linearGradient id="worker" x1="0" y1="0" x2="1" y2="1">
        <stop offset="0" stop-color="#e2b35a"/>
        <stop offset="1" stop-color="#b98940"/>
      </linearGradient>
      <linearGradient id="corner" x1="0" y1="0" x2="1" y2="1">
        <stop offset="0" stop-color="#d8d6d2"/>
        <stop offset="1" stop-color="var(--paper)"/>
      </linearGradient>
      <radialGradient id="crystals" cx=".45" cy=".4" r=".6">
        <stop offset="0" stop-color="#f4ead0"/>
        <stop offset="1" stop-color="#cdbb90"/>
      </radialGradient>
    </defs>

    <rect width="800" height="1130" fill="url(#saltbed)" role="img" aria-label="Close-up of coarse mineral salt crystals"/>
    <polygon points="0,0 800,0 800,130 590,440 0,530" fill="url(#valley)" role="img" aria-label="Salt terraces in a mountain valley under a cloudy sky"/>
    <polygon points="0,530 590,440 800,130 800,175 612,470 0,558" fill="var(--pink)"/>
    <polygon points="800,560 800,770 640,1130 585,1130 700,700" fill="var(--pink-deep)"/>
    <polygon points="800,770 800,1130 640,1130" fill="url(#corner)"/>

    <polygon points="0,262 600,244 596,304 0,322" fill="var(--yellow)" opacity=".92"/>

    <g transform="rotate(-8 690 300)">
      <rect x="605" y="215" width="185" height="170" fill="#fff"/>
      <rect x="613" y="223" width="169" height="154" fill="url(#terraces)" role="img" aria-label="White salt pools on the terraces"/>
    </g>
    <g transform="rotate(6 630 420)">
      <rect x="550" y="355" width="160" height="140" fill="#fff"/>
      <rect x="558" y="363" width="144" height="124" fill="url(#worker)" role="img" aria-label="Salt worker harvesting by hand"/>
    </g>

    <circle cx="615" cy="830" r="160" fill="#5f6062"/>
    <circle cx="615" cy="830" r="145" fill="#9a9b9d"/>
    <circle cx="615" cy="830" r="132" fill="url(#crystals)" role="img" aria-label="Bowl filled with coarse salt crystals"/>
  </svg>

  <h1 class="title">VENTO ZOUT</h1>
  <p class="tagline">UIT DE HEILIGE VALLEI VAN DE INCAS</p>

  <p class="intro">Op ongeveer 3500 meter hoogte in het Andes gebergte van Peru ontspringt een natuurlijk stroompje met het meest zuivere en complete</p>

  <h2 class="product-name">Mineral Keukenzout</h2>
  <p class="product-lead">Bevat 84 mineralen en sporen elementen:</p>
  <ul class="minerals">
    <li>Calcium</li><li>Zink</li>
    <li>Ijzer</li><li>Magnesium</li>
    <li style="grid-column: 1 / 3">Jodium<span class="dose">(3.5mg / 100gm)</span></li>
  </ul>

  <ul class="benefits">
    <li><svg width="16" height="14" viewBox="0 0 16 14"><path d="M1 8 L6 13 L15 1" fill="none" stroke="var(--ink)" stroke-width="2"/></svg>Heel smaakvol</li>
    <li><svg width="16" height="14" viewBox="0 0 16 14"><path d="M1 8 L6 13 L15 1" fill="none" stroke="var(--ink)" stroke-width="2"/></svg>Minder natrium</li>
    <li><svg width="16" height="14" viewBox="0 0 16 14"><path d="M1 8 L6 13 L15 1" fill="none" stroke="var(--ink)" stroke-width="2"/></svg><span>Direct van de lokale mensen<br>in Peru</span></li>
    <li><svg width="16" height="14" viewBox="0 0 16 14"><path d="M1 8 L6 13 L15 1" fill="none" stroke="var(--ink)" stroke-width="2"/></svg><span>Afkomstig van een oude<br>schone oceaan</span></li>
    <li><svg width="16" height="14" viewBox="0 0 16 14"><path d="M1 8 L6 13 L15 1" fill="none" stroke="var(--ink)" stroke-width="2"/></svg>Natuurlijk proces van winning</li>
    <li><svg width="16" height="14" viewBox="0 0 16 14"><path d="M1 8 L6 13 L15 1" fill="none" stroke="var(--ink)" stroke-width="2"/></svg>Met de hand geoogst</li>
  </ul>

  <div class="brand">
    <p class="brand-name">Valecresta</p>
    <p class="brand-url">www.valecrestafoods.com</p>
  </div>
</article>
</body>
</html>
```